Package Label Design Needed for FRUIT JELLY

We need label design for Fruit Jelly Jar and each Fruit Jelly cup(6 flavored cups). Our product is a jar with 6 assorted fruit flavored jellies. (flavors are strawberry, pineapple, mango, lychee, apple, grape) and we need design for :
1) jar label
2) each jelly cup label
All of above (1) & (2) artwork templates and our old labels are attached.
Each jelly is in a heart shaped cup.
Artwork template(dieline) is attached.
Label needs to have followings:
Company logo: Teliv (Attached)
Product Name: Snappy Pebbles (Attached) -- TM
Flavor Name: Strawberry or Apple or etc
Old labels are attached to give you an idea. Contents in the old need be pasted in your labels (nutrition facts, net weight etc).
On the label for jar, following phrase must be included:
"Snappy Pebbles TM
with Hidden Treasure Inside"
Coconut Chunk is included inside jelly
Made of Real Fruit Juice
Distributed by Teliv, Inc. Brenmoor, CA 90417(Back side bottom. Under Nutritional Facts)
Made in Taiwan
(Somewhere in Front)
Low Sugar
0% Transfat
0% Cholesterol
All Natural
Keep refrigerated for an even better taste
Target Market(s)
Both kids and adults who love snacking or who love fun, tasty, fruity snacks.
Industry/Entity Type
Product
Colors
Designer to choose colors to be used in the design.
Requirements
Must have
- Our company logo: Teliv
- Product Name: Snappy Pebbles
- ETC

```html
<!DOCTYPE html>
<html lang="en">
<head>
<meta charset="utf-8">
<title>Snappy Pebbles – Jar and Cup Labels</title>
<link rel="stylesheet" href="https://fonts.googleapis.com/css2?family=Chewy&family=Courier+Prime:wght@700&family=Roboto+Condensed:wght@400;700;900&display=swap">
<style>
:root{
  --ink:#1d1d1d;
  --paper:#ffffff;
  --brand-brown:#6b3d12;
  --lime:#d6f53c;
  --green:#6cc31c;
  --red:#e2242b;
  --purple:#7b2d8e;
  --dash:#555;
}
*{box-sizing:border-box;margin:0;padding:0}
html,body{width:1200px;height:849px;overflow:hidden;background:var(--paper)}
body{position:relative;font-family:"Roboto Condensed",Arial,sans-serif;color:var(--ink)}
.shapes{position:absolute;left:0;top:0}
.abs{position:absolute}

.size-note{left:98px;top:212px;font-weight:900;font-size:15px;letter-spacing:.2px}

/* cup labels */
.cup{position:absolute;width:172px;height:111px}
.cup-logo{position:absolute;top:19px;left:0;width:100%;text-align:center;font-family:"Chewy",sans-serif;font-size:13px;line-height:14px;color:var(--ink)}
.cup-name{position:absolute;top:34px;left:0;width:100%;text-align:center;font-family:"Chewy",sans-serif;font-size:16px;line-height:15px;color:var(--brand-brown)}
.cup-flavor{position:absolute;top:68px;left:50%;transform:translateX(-50%);background:var(--purple);color:#fff;font-size:8.5px;font-weight:700;padding:1px 7px;border-radius:2px;letter-spacing:.5px;white-space:nowrap}

/* jar label */
.nutrition{left:259px;top:271px;width:160px;background:#fff;border:1.5px solid var(--ink);padding:3px 5px 4px;font-size:8px;line-height:1.15}
.nutrition h2{font-family:"Roboto Condensed",sans-serif;font-weight:900;font-size:20px;line-height:21px;border-bottom:1px solid var(--ink);letter-spacing:-.3px}
.nutrition .serving{font-size:6.5px;line-height:1.15;border-bottom:5px solid var(--ink);padding:2px 0}
.nutrition .row{display:flex;justify-content:space-between;border-bottom:.8px solid var(--ink);padding:1px 0}
.nutrition .row.indent{padding-left:10px}
.nutrition .row.thick{border-bottom:3px solid var(--ink)}
.nutrition .row.last{border-bottom:none}
.nutrition b{font-weight:700}

.jar-logo{left:178px;top:508px;font-family:"Chewy",sans-serif;font-size:27px;line-height:30px;color:var(--ink)}
.distributor{left:300px;top:504px;width:100px;text-align:center;font-size:7.5px;font-weight:700;line-height:1.3}
.origin{left:300px;top:553px;width:100px;text-align:center;font-size:7.5px;font-weight:700}

.front-logo{left:504px;top:268px;width:120px;text-align:center;font-family:"Chewy",sans-serif;font-size:34px;line-height:38px;color:var(--ink)}
.real-juice{left:440px;top:318px;transform:rotate(-14deg);color:var(--red);font-weight:900;font-size:10px;line-height:1.1;text-align:center}
.claims{left:712px;top:316px;width:80px;color:var(--green);font-weight:900;font-size:9.5px;line-height:1.25;text-align:center}
.product-name{left:440px;top:345px;width:340px;text-align:center;font-family:"Chewy",sans-serif;font-size:74px;line-height:74px;font-weight:400;color:var(--brand-brown);letter-spacing:1px}
.tm{left:764px;top:470px;font-size:9px;font-weight:700}
.treasure{left:462px;top:538px;width:290px;height:26px;background:var(--ink);color:#fff;border-radius:4px;text-align:center;font-family:"Chewy",sans-serif;font-size:17px;line-height:26px;letter-spacing:.6px;white-space:nowrap}

.info-box{left:806px;width:292px;background:var(--lime);font-family:"Courier Prime",monospace;font-size:12px;line-height:14px;text-align:center}
.info-box h3{background:var(--ink);color:#fff;font-family:"Courier Prime",monospace;font-size:15px;font-weight:700;padding:2px 0;letter-spacing:.5px}
.info-box p{padding:4px 6px}
.ingredients{top:290px}
.storage{top:426px}
</style>
</head>
<body>

<svg class="shapes" width="1200" height="849" viewBox="0 0 1200 849">
  <defs>
    <linearGradient id="fruit-warm" x1="0" y1="0" x2="1" y2="1">
      <stop offset="0" stop-color="#8e3fa5"/>
      <stop offset=".35" stop-color="#f7c12e"/>
      <stop offset=".7" stop-color="#9ccf3c"/>
      <stop offset="1" stop-color="#e8452f"/>
    </linearGradient>
    <linearGradient id="fruit-centre" x1="0" y1="0" x2="1" y2="1">
      <stop offset="0" stop-color="#f6a623"/>
      <stop offset=".4" stop-color="#fbe07a"/>
      <stop offset=".75" stop-color="#e8412f"/>
      <stop offset="1" stop-color="#8bc34a"/>
    </linearGradient>
    <linearGradient id="fruit-right" x1="0" y1="0" x2="1" y2="1">
      <stop offset="0" stop-color="#f3b03a"/>
      <stop offset=".5" stop-color="#e94f37"/>
      <stop offset="1" stop-color="#7e3f98"/>
    </linearGradient>
    <path id="cup-shape" d="M10,60 C0,18 60,0 86,16 C112,0 172,18 162,60 C155,95 115,111 86,105 C57,111 17,95 10,60Z"/>
  </defs>

  <!-- cup labels, top row -->
  <g transform="translate(274,69)"><use href="#cup-shape" fill="url(#fruit-warm)" stroke="var(--dash)" stroke-dasharray="3 2" role="img" aria-label="Apple cup label fruit illustration"/></g>
  <g transform="translate(490,69)"><use href="#cup-shape" fill="url(#fruit-warm)" stroke="var(--dash)" stroke-dasharray="3 2" role="img" aria-label="Grape cup label fruit illustration"/></g>
  <g transform="translate(710,69)"><use href="#cup-shape" fill="url(#fruit-warm)" stroke="var(--dash)" stroke-dasharray="3 2" role="img" aria-label="Lychee cup label fruit illustration"/></g>
  <!-- cup labels, bottom row -->
  <g transform="translate(300,650)"><use href="#cup-shape" fill="url(#fruit-warm)" stroke="var(--dash)" stroke-dasharray="3 2" role="img" aria-label="Mango cup label fruit illustration"/></g>
  <g transform="translate(510,650)"><use href="#cup-shape" fill="url(#fruit-warm)" stroke="var(--dash)" stroke-dasharray="3 2" role="img" aria-label="Pineapple cup label fruit illustration"/></g>
  <g transform="translate(722,650)"><use href="#cup-shape" fill="url(#fruit-warm)" stroke="var(--dash)" stroke-dasharray="3 2" role="img" aria-label="Strawberry cup label fruit illustration"/></g>

  <!-- jar label outline -->
  <path d="M74,252 L403,252 Q604,212 806,252 L1114,252 L1114,574 L806,574 Q604,604 403,574 L74,574 Z" fill="#fff" stroke="var(--dash)" stroke-width="1.2" stroke-dasharray="4 3"/>
  <rect x="82" y="259" width="176" height="238" fill="url(#fruit-warm)" role="img" aria-label="Pile of grapes, bananas, oranges, kiwis and cherries"/>
  <path d="M420,252 Q604,220 797,252 L797,574 Q604,598 420,574 Z" fill="url(#fruit-centre)" role="img" aria-label="Burst of colourful cut fruit and berries behind the product name"/>
  <rect x="797" y="259" width="310" height="310" fill="url(#fruit-right)" role="img" aria-label="Assorted fruit pieces"/>
  <line x1="420" y1="252" x2="420" y2="574" stroke="var(--dash)" stroke-dasharray="4 3"/>
  <line x1="797" y1="252" x2="797" y2="574" stroke="var(--dash)" stroke-dasharray="4 3"/>
</svg>

<div class="abs size-note">SIZE:235X76mm</div>

<!-- cup label text -->
<div class="cup" style="left:274px;top:69px"><div class="cup-logo">Teliv</div><div class="cup-name">Snappy<br>Pebbles</div><div class="cup-flavor">APPLE</div></div>
<div class="cup" style="left:490px;top:69px"><div class="cup-logo">Teliv</div><div class="cup-name">Snappy<br>Pebbles</div><div class="cup-flavor">GRAPE</div></div>
<div class="cup" style="left:710px;top:69px"><div class="cup-logo">Teliv</div><div class="cup-name">Snappy<br>Pebbles</div><div class="cup-flavor">LYCHEE</div></div>
<div class="cup" style="left:300px;top:650px"><div class="cup-logo">Teliv</div><div class="cup-name">Snappy<br>Pebbles</div><div class="cup-flavor">MANGO</div></div>
<div class="cup" style="left:510px;top:650px"><div class="cup-logo">Teliv</div><div class="cup-name">Snappy<br>Pebbles</div><div class="cup-flavor">PINEAPPLE</div></div>
<div class="cup" style="left:722px;top:650px"><div class="cup-logo">Teliv</div><div class="cup-name">Snappy<br>Pebbles</div><div class="cup-flavor">STRAWBERRY</div></div>

<!-- jar label: back panel -->
<section class="abs nutrition">
  <h2>Nutrition Facts</h2>
  <div class="serving">Serving size 1 cup (42.5g)<br>Servings per container 6</div>
  <div class="row"><b>Amount Per Serving</b></div>
  <div class="row thick"><b>Calories</b><span>15.67</span></div>
  <div class="row"><span></span><b>% Daily Value*</b></div>
  <div class="row"><span><b>Total Fat</b> 0g</span><span>0%</span></div>
  <div class="row indent"><span>Saturated Fat 0g</span><span>0%</span></div>
  <div class="row indent"><span>Trans Fat 0g</span><span></span></div>
  <div class="row"><span><b>Cholesterol</b> 0mg</span><span>0%</span></div>
  <div class="row"><span><b>Sodium</b> 17.6mg</span><span>0.37%</span></div>
  <div class="row"><span><b>Total Carbohydrate</b> 8.1g</span><span>2.54%</span></div>
  <div class="row indent"><span>Dietary Fiber 2.2g</span><span>11.68%</span></div>
  <div class="row indent thick"><span>Sugars 4.6g</span><span></span></div>
  <div class="row last"><span><b>Protein</b> 0g</span><span>0%</span></div>
</section>
<div class="abs jar-logo">Teliv</div>
<div class="abs distributor">DISTRIBUTED BY:<br>Teliv, Inc.<br>Brenmoor, CA 90417</div>
<div class="abs origin">Made in Taiwan</div>

<!-- jar label: front panel -->
<div class="abs front-logo">Teliv</div>
<div class="abs real-juice">MADE WITH REAL<br>FRUIT JUICE!</div>
<div class="abs claims">ALL NATURAL<br>LOW SUGAR<br>0% TRANS FAT<br>0% CHOLESTEROL</div>
<h1 class="abs product-name">Snappy<br>Pebbles</h1>
<div class="abs tm">TM</div>
<div class="abs treasure">WITH HIDDEN TREASURES!</div>

<!-- jar label: side panel -->
<section class="abs info-box ingredients">
  <h3>ingredients</h3>
  <p>seaweed extract, water, sugar, fructose, coconut pieces, natural flavors of grape, green apple, lychee mango, pineapple, and strawberry, food coloring (red#40, blue#1, yellow#5), and no animal sources</p>
</section>
<section class="abs info-box storage">
  <h3>storage and caution</h3>
  <p>Keep refrigerated for an even better taste. Each piece does contain fruit chunks and may not be chewable for very young children.</p>
</section>

</body>
</html>
```